Moxy Fen needs some awesome stationary

Do you have what it takes to get my brand? You either do or you don't, have a crack at a design and you my just win my business.

I don't want to waste your or my time, so put your creative genius on either a business card or envelope.

I however need a package of stationary that follows the same brand. I will message you to complete the remaining should I like your first submission.

Here is what I need, have a go!

Basically I need the following for my small business based in melbourne.
- Letterhead (printer ready and MS Word)
- Business Card
- Compliments Slip
- Envelope
- Proposal Cover Page (MS Word only)
- Presentation Folder
- Marbled Fox Cards
- Student Name Tent
- Index Cards
- Vell-Ka

I am establishing the brand and it must be modern, professional but also relaxed; that is not formal and not corporate. It represents a company are leaders, but small enough to care and operate like a bunch of friends. We are bringing people and conversations back to business, and turfing out all the bureaucracy and crazy and wasteful procedures. Its about "lets talk and figure it out together and find even better ways".

Target Market(s)

Mainly companies that build software products, but Agile practices are used in many other industries (even graphic design projects)

Industry/Entity Type

Information Technology

Font styles to use
Sans Serif

Colors
3176b5
aaaaaa

Requirements
Must have
• I like curves and circles and not boxes or rectangles.
• I want a colour rich design with my brand colours, but it must be balanced.
• I want more modern than traditional, but simple modern
Should not have
• Not corporate
• Please don't waste my time if your not going to think about it.
• Don't mess with my primary logo
• Don't change my colours
• Don't overlay logo on image

```html
<!DOCTYPE html>
<html lang="en">
<head>
<meta charset="utf-8">
<title>Moxy Fen — Business Card</title>
<link href="https://fonts.googleapis.com/css2?family=Open+Sans:wght@400;600;700&display=swap" rel="stylesheet">
<style>
  :root {
    --brand-blue: #2c5ba3;
    --brand-grey: #9aa3b0;
    --ink: #4a4a4a;
    --rule: #b9c0ca;
    --paper: #ffffff;
    --backdrop: #ebe8e4;
  }
  * { margin: 0; padding: 0; box-sizing: border-box; }
  html, body {
    width: 1200px; height: 987px; overflow: hidden;
    background: var(--backdrop);
    font-family: "Open Sans", Arial, sans-serif;
  }
  .card {
    position: absolute;
    background: var(--paper);
    box-shadow: 0 2px 6px rgba(0,0,0,.18);
    overflow: hidden;
  }
  .card--front { left: 293px; top: 131px; width: 615px; height: 350px; }
  .card--back  { left: 292px; top: 506px; width: 616px; height: 351px; }

  /* front */
  .brand {
    position: absolute; right: 37px; top: 138px;
    display: flex; align-items: center; gap: 12px;
  }
  .brand__dot { width: 26px; height: 26px; border-radius: 50%; background: var(--brand-blue); }
  .brand__name { font-size: 34px; font-weight: 600; color: var(--brand-blue); line-height: 1; }

  .tab {
    position: absolute; left: -2px; top: 173px; width: 16px; height: 47px;
    background: var(--brand-blue); border-radius: 0 24px 24px 0;
  }
  .person { position: absolute; left: 33px; top: 173px; }
  .person__name { font-size: 21px; font-weight: 600; color: var(--brand-blue); line-height: 26px; }
  .person__role { font-size: 16px; color: var(--brand-grey); line-height: 22px; }
  .rule { position: absolute; left: 33px; right: 37px; top: 225px; border-top: 1px solid var(--rule); }

  .contacts { position: absolute; left: 33px; top: 235px; list-style: none; }
  .contacts li {
    display: flex; align-items: center; gap: 9px;
    height: 23.5px; font-size: 15px; color: var(--ink);
  }
  .contacts svg { width: 15px; height: 15px; fill: var(--brand-blue); flex: none; }

  .address {
    position: absolute; right: 37px; top: 259px;
    font-style: normal; text-align: right; font-size: 15px; line-height: 22px; color: var(--ink);
  }

  /* back */
  .back-band { position: absolute; inset: 0; }
  .back-band path { fill: var(--brand-blue); }
  .back-title {
    position: absolute; left: 548px; top: 175px;
    transform: translate(-50%, -50%) rotate(-90deg);
    display: flex; flex-direction: column; align-items: center;
    color: var(--paper); white-space: nowrap;
  }
  .back-title__name { font-size: 46px; font-weight: 600; line-height: 50px; }
  .back-title__web { font-size: 14px; letter-spacing: 3.5px; line-height: 20px; }
</style>
</head>
<body>

<section class="card card--front">
  <div class="brand">
    <span class="brand__dot"></span>
    <span class="brand__name">Moxy Fen</span>
  </div>

  <span class="tab"></span>
  <div class="person">
    <p class="person__name">Dana Holloway</p>
    <p class="person__role">CEO, Professional Agile Coach</p>
  </div>
  <div class="rule"></div>

  <ul class="contacts">
    <li>
      <svg viewBox="0 0 16 16"><path d="M3.5 1l2.6 3-1.4 1.9c.9 2 2.4 3.5 4.4 4.4L11 8.9l3 2.6-1.4 2.5C7.3 14 2 8.7 2 3.3z"/></svg>
      1300 555 019
    </li>
    <li>
      <svg viewBox="0 0 16 16"><path d="M4.5 0h7a1 1 0 0 1 1 1v14a1 1 0 0 1-1 1h-7a1 1 0 0 1-1-1V1a1 1 0 0 1 1-1zm.6 2v10.5h5.8V2zM8 13.3a.9.9 0 1 0 0 1.8.9.9 0 0 0 0-1.8z"/></svg>
      +61 400 555 218
    </li>
    <li>
      <svg viewBox="0 0 16 16"><path d="M1 3.5h14v1L8 9 1 4.5zM1 6l7 4.5L15 6v6.5H1z"/></svg>
      dana@moxyfen.com.au
    </li>
    <li>
      <svg viewBox="0 0 16 16"><path d="M8 1a7 7 0 1 0 0 14A7 7 0 0 0 8 1zm-1 2.3c-.4 1-1.5 1.2-1.6 2.3.3 1 1.6.7 2 1.6-.2 1.1-1.3 1.6-1 2.8.3 1 .2 2-.3 2.6A5 5 0 0 1 7 3.3zm2.5.2a5 5 0 0 1 3.3 5.3c-.8-.6-1.6-.2-2.2.5-.7-.5-.3-1.8-1.3-2.2-.8-.3-1.2-1-.7-1.7.5-.6 1.2-.9.9-1.9z"/></svg>
      www.moxyfen.com.au
    </li>
  </ul>

  <address class="address">
    PO Box 4417<br>
    Larkfield North<br>
    VIC 3199, Australia
  </address>
</section>

<section class="card card--back">
  <svg class="back-band" viewBox="0 0 616 351" width="616" height="351" aria-hidden="true">
    <path d="M350 0 Q470 175 345 351 L616 351 L616 0 Z"/>
  </svg>
  <div class="back-title">
    <span class="back-title__name">Moxy Fen</span>
    <span class="back-title__web">www.moxyfen.com.au</span>
  </div>
</section>

</body>
</html>
```